Homepage and Interior Page Design for DashLoom

We will provide all logos, graphics and images as well as a wireframe of the desired homepage layout. Deliverables should be two well formated Photoshop files will well named layers, one for the homepage and one for an interior page. The "Puzzle Animation" will be developed separately. This will be a puzzle that breaks apart and reassembles to rotate the images. Here is the old site: https://www.dashloom-example.com/

Target Market(s)

Small to mid sized manufacturers.

Number of Pages Required

2 page

Font styles to use
Sans Serif

Colors

Designer to choose colors to be used in the design.

Requirements
Must have
• 2 layered photoshop files ready for slicing to HTML will well labeled layers
Nice to have
• If you are interested in creating the animation as a separate project, let me know.

```html
<!DOCTYPE html>
<html lang="en">
<head>
<meta charset="utf-8">
<title>DashLoom – Contract Packaging &amp; Assembly</title>
<link href="https://fonts.googleapis.com/css2?family=Lato:wght@400;700;900&display=swap" rel="stylesheet">
<style>
  :root{
    --purple:#4b1d6f;
    --crimson:#b3124f;
    --ink:#222;
    --text:#3c3c3c;
    --light:#f3f3f3;
    --topbar:#ececec;
    --footer:#2b2b2b;
    --footer-text:#d9d9d9;
    --white:#fff;
  }
  *{box-sizing:border-box;margin:0;padding:0}
  html,body{width:1002px;height:1200px;overflow:hidden;background:var(--white)}
  body{font-family:'Lato',sans-serif;color:var(--text);position:relative}
  a{color:inherit;text-decoration:none}

  .top-bar{position:absolute;left:0;top:0;width:1002px;height:41px;background:var(--topbar)}
  .top-phone{position:absolute;left:62px;top:13px;font-size:13px;font-weight:700;color:#333;display:flex;align-items:center;gap:8px}
  .social-square{position:absolute;top:12px;width:16px;height:16px;background:#666;border-radius:3px}
  .top-bar .social-square{left:922px}

  .brand-tab{position:absolute;left:398px;top:15px;width:208px;height:46px;background:var(--white);border-radius:10px 10px 0 0;display:flex;align-items:center;justify-content:center}
  .brand-name{font-size:30px;font-weight:900;color:var(--crimson);letter-spacing:.5px}

  .main-nav{position:absolute;left:62px;top:80px;width:878px;display:flex;justify-content:space-between;font-size:11.5px;font-weight:700;color:var(--ink)}

  .hero{position:absolute;left:0;top:113px;width:1002px;height:440px;background:var(--light)}
  .hero-title{position:absolute;left:62px;top:110px;width:400px;font-size:37px;line-height:38px;font-weight:900;color:var(--purple)}
  .hero-text{position:absolute;left:62px;top:192px;width:380px;font-size:14px;line-height:21.6px}
  .btn{display:inline-block;background:var(--crimson);color:var(--white);font-size:11.5px;font-weight:700;border-radius:13px;width:103px;height:26px;line-height:26px;text-align:center}
  .hero .btn{position:absolute;left:64px;top:297px}
  .slider-dots{position:absolute;left:62px;top:379px;display:flex;gap:6px}
  .slider-dots span{width:9px;height:9px;border-radius:50%;background:#aaa}
  .slider-dots span.active{background:var(--purple)}
  .hero-visual{position:absolute;left:474px;top:92px;width:468px;height:330px;background:linear-gradient(135deg,#d4501f 0%,#e2612c 40%,#9aa3ab 70%,#e8744a 100%);border-radius:4px}

  .services{position:absolute;left:62px;top:591px;width:878px;display:flex;justify-content:space-between}
  .service-card{width:202px;height:370px;background:var(--light);border-radius:8px;overflow:hidden;text-align:center}
  .service-head{height:54px;background:linear-gradient(90deg,var(--purple),var(--crimson));color:var(--white);font-size:15.5px;font-weight:900;line-height:17px;display:flex;align-items:center;justify-content:center;padding:0 20px}
  .service-img{height:144px}
  .img-fasteners{background:linear-gradient(160deg,#c9ccd0,#8b96a1)}
  .img-assembly{background:linear-gradient(160deg,#c7d23b,#d98a27)}
  .img-pallets{background:linear-gradient(160deg,#b09a78,#d8c6a4)}
  .img-kitting{background:linear-gradient(160deg,#e9e7e4,#b7a48b)}
  .service-text{font-size:12.5px;line-height:18.5px;padding:11px 12px 0;height:132px}
  .service-card .btn{margin-top:1px}

  .site-footer{position:absolute;left:0;top:994px;width:1002px;height:206px;background:var(--footer);color:var(--footer-text);font-size:11.5px}
  .footer-col{position:absolute;top:32px}
  .footer-col h4{color:var(--white);font-size:12.5px;font-weight:700;margin-bottom:6px}
  .footer-col li{list-style:none;line-height:22.4px}
  .footer-brand{left:64px;top:50px}
  .footer-brand .brand-name{color:var(--white);font-size:28px;display:block;margin-bottom:10px}
  .footer-brand p{line-height:19px}
  .footer-brand .social-square{position:static;display:block;margin-top:16px;background:#ddd}
  .col-sitemap{left:286px}
  .col-contact{left:522px}
  .contact-line{display:flex;align-items:center;gap:16px}
  .col-signup{left:738px;width:203px}
  .email-field{width:203px;height:33px;background:var(--white);border-radius:9px;color:#444;font-size:11.5px;line-height:33px;padding-left:14px;margin-top:2px}
  .col-signup .btn{position:absolute;right:0;top:88px;width:75px;height:31px;line-height:31px;border-radius:10px}
</style>
</head>
<body>
  <header class="top-bar">
    <div class="top-phone">
      <svg width="10" height="10" viewBox="0 0 24 24"><path fill="#b3124f" d="M6.6 10.8a15 15 0 006.6 6.6l2.2-2.2a1 1 0 011-.25 11.4 11.4 0 003.6.6 1 1 0 011 1V20a1 1 0 01-1 1A17 17 0 013 4a1 1 0 011-1h3.5a1 1 0 011 1c0 1.25.2 2.45.6 3.6a1 1 0 01-.25 1z"/></svg>
      555.210.3870
    </div>
    <span class="social-square"></span>
  </header>
  <div class="brand-tab"><span class="brand-name">DashLoom</span></div>
  <nav class="main-nav">
    <a href="#">CONTRACT PACKAGING</a>
    <a href="#">PRODUCT ASSEMBLY</a>
    <a href="#">CUSTOM PALLETS &amp; CRATES</a>
    <a href="#">INVENTORY MANAGEMENT &amp; FULFILLMENT</a>
    <a href="#">ABOUT US</a>
    <a href="#">CONTACT US</a>
  </nav>

  <section class="hero">
    <h1 class="hero-title">We put all the pieces together</h1>
    <p class="hero-text">DashLoom is your one-stop source, from manufacturing to assembly to retail-ready packaging. We case-pack, print all standard bar code label formats, palletize and drop ship anywhere in the world.</p>
    <a class="btn" href="#">READ MORE</a>
    <div class="slider-dots"><span class="active"></span><span></span><span></span><span></span></div>
    <div class="hero-visual" role="img" aria-label="Puzzle-piece collage of an orange parts tray holding screws and plastic anchors"></div>
  </section>

  <main class="services">
    <article class="service-card">
      <h2 class="service-head">CONTRACT PACKAGING</h2>
      <div class="service-img img-fasteners" role="img" aria-label="Bagged bolts, nuts and hardware"></div>
      <p class="service-text">We cover the spectrum of visible retail packaging, from blisters to clamshells to stretchpak, pouches, and bags. Ask about our cost-free tooling solutions.</p>
      <a class="btn" href="#">READ MORE</a>
    </article>
    <article class="service-card">
      <h2 class="service-head">PRODUCT ASSEMBLY</h2>
      <div class="service-img img-assembly" role="img" aria-label="Assembled retail display card with a maple syrup bottle"></div>
      <p class="service-text">We cover the spectrum of visible retail packaging, from blisters to clamshells to stretchpak, pouches, and bags. Ask about our cost-free tooling solutions.</p>
      <a class="btn" href="#">READ MORE</a>
    </article>
    <article class="service-card">
      <h2 class="service-head">CUSTOM PALLETS AND CRATES</h2>
      <div class="service-img img-pallets" role="img" aria-label="Stacks of wooden pallets in a warehouse"></div>
      <p class="service-text">We cover the spectrum of visible retail packaging, from blisters to clamshells to stretchpak, pouches, and bags. Ask about our cost-free tooling solutions.</p>
      <a class="btn" href="#">READ MORE</a>
    </article>
    <article class="service-card">
      <h2 class="service-head">CUSTOM KITTING</h2>
      <div class="service-img img-kitting" role="img" aria-label="Open cardboard box filled with bagged kit parts"></div>
      <p class="service-text">We cover the spectrum of visible retail packaging, from blisters to clamshells to stretchpak, pouches, and bags. Ask about our cost-free tooling solutions.</p>
      <a class="btn" href="#">READ MORE</a>
    </article>
  </main>

  <footer class="site-footer">
    <div class="footer-col footer-brand">
      <span class="brand-name">DashLoom</span>
      <p>Copyright © 2019 Company Name<br>All rights Reserved.</p>
      <span class="social-square"></span>
    </div>
    <div class="footer-col col-sitemap">
      <h4>SITE MAP</h4>
      <ul>
        <li>Contract Packaging</li>
        <li>Product Assembly</li>
        <li>Custom Pallets &amp; Crates</li>
        <li>Inventory Management &amp; Fulfillment</li>
        <li>About Us</li>
        <li>Contact Us</li>
      </ul>
    </div>
    <div class="footer-col col-contact">
      <h4>CONTACT INFO</h4>
      <ul>
        <li>4470 Quarry Mill Rd</li>
        <li>Fairbrook, Ohio 44901</li>
        <li class="contact-line" style="margin-top:4px">
          <svg width="10" height="10" viewBox="0 0 24 24"><path fill="#ddd" d="M6.6 10.8a15 15 0 006.6 6.6l2.2-2.2a1 1 0 011-.25 11.4 11.4 0 003.6.6 1 1 0 011 1V20a1 1 0 01-1 1A17 17 0 013 4a1 1 0 011-1h3.5a1 1 0 011 1c0 1.25.2 2.45.6 3.6a1 1 0 01-.25 1z"/></svg>
          555.210.3870</li>
        <li class="contact-line" style="margin-top:4px">
          <svg width="11" height="9" viewBox="0 0 22 16"><rect width="22" height="16" rx="1" fill="#ddd"/><path d="M1 1l10 8 10-8" stroke="#2b2b2b" stroke-width="2" fill="none"/></svg>
          hello@dashloom-example.com</li>
      </ul>
    </div>
    <div class="footer-col col-signup">
      <h4>EMAIL SIGN UP</h4>
      <div class="email-field">Enter Email Address</div>
      <a class="btn" href="#">SIGN UP</a>
    </div>
  </footer>
</body>
</html>
```